Willow Creek Gatherings Event Planning in need of a design!!

Event Planning company, does a variety of events. I like simple more rustic designs focused on almond blossoms. We are based out of Northern California, the heart of almond country. I would like to see colors in light pinks, beige, light browns, whites or creams. the final design should communicate rustic simplicity. Below are some pictures of Almond blossoms and design ideas I prefer the one called Tulip Grove. Thanks

Target Market(s)

Women in the mid twenties and older. They should be in the upper middle class in need of an amazing party design and coordinator

Industry/Entity Type

Event Planning

Contact Information for Business Card

Maren Lockwood 530-624-0295almondbaffairs@gmail.comalmondblossomaffairs.com

Font styles to use
Other font styles liked:
• Amatic SC

Requirements
Must have
• almond blossom
• my information
• simplicity
Nice to have
• rustic design
• vintage feel
• whimsical
Should not have
• i like pink but not over the top

```html
<!DOCTYPE html>
<html lang="en">
<head>
<meta charset="utf-8">
<title>Willow Creek Gatherings – Business Card</title>
<link rel="stylesheet" href="https://fonts.googleapis.com/css2?family=Source+Sans+3:wght@400&display=swap">
<style>
  :root {
    --page-bg: #ece8e3;
    --card-white: #ffffff;
    --blossom-pink: #f27ea4;
    --contact-teal: #5fb0a2;
    --orchard-green: #7e9a6a;
    --orchard-sky: #cfe0ea;
    --orchard-bloom: #e9dfe3;
    --orchard-shade: #3a3f33;
    --card-shadow: rgba(60, 40, 30, 0.18);
  }
  html, body {
    margin: 0;
    padding: 0;
    width: 1200px;
    height: 676px;
    overflow: hidden;
    background: var(--page-bg);
    font-family: "Source Sans 3", sans-serif;
  }
  .sheet {
    position: relative;
    width: 1200px;
    height: 676px;
  }
  .card {
    position: absolute;
    top: 188px;
    width: 520px;
    height: 300px;
    background: var(--card-white);
    box-shadow: 0 6px 18px var(--card-shadow);
    overflow: hidden;
  }
  .card--front { left: 60px; }
  .card--back  { left: 620px; }
  .card-art { position: absolute; left: 0; top: 0; }

  .front-name {
    position: absolute;
    right: 34px;
    top: 110px;
    margin: 0;
    font-size: 30px;
    line-height: 36px;
    font-weight: 400;
    color: var(--blossom-pink);
    letter-spacing: 0.5px;
    white-space: nowrap;
  }
  .contact-list {
    position: absolute;
    right: 30px;
    bottom: 30px;
    margin: 0;
    padding: 0;
    list-style: none;
  }
  .contact-list li {
    display: flex;
    justify-content: flex-end;
    align-items: center;
    gap: 10px;
    font-size: 17px;
    line-height: 24px;
    color: var(--contact-teal);
    white-space: nowrap;
  }
  .contact-icon { display: block; width: 14px; height: 14px; flex: none; }

  .back-name {
    position: absolute;
    left: 26px;
    top: 14px;
    margin: 0;
    font-size: 22px;
    font-weight: 400;
    color: var(--blossom-pink);
  }
</style>
</head>
<body>
<main class="sheet">

  <section class="card card--front" aria-label="Business card front">
    <svg class="card-art" width="520" height="300" viewBox="0 0 520 300">
      <defs>
        <linearGradient id="orchard-front" x1="0" y1="0" x2="1" y2="1">
          <stop offset="0" stop-color="var(--orchard-sky)"/>
          <stop offset="0.45" stop-color="var(--orchard-bloom)"/>
          <stop offset="1" stop-color="var(--orchard-green)"/>
        </linearGradient>
      </defs>
      <polygon class="accent-stripe" points="0,0 214,0 272,178 0,212" fill="var(--blossom-pink)"/>
      <polygon class="orchard-photo" role="img" aria-label="Photo of an almond orchard in bloom, rows of white-blossomed trees along a path"
               points="0,0 200,0 260,168 0,198" fill="url(#orchard-front)"/>
    </svg>
    <h1 class="front-name">Maren Lockwood</h1>
    <ul class="contact-list">
      <li><span>530-817-4362</span>
        <svg class="contact-icon" viewBox="0 0 14 14" aria-hidden="true"><rect x="3" y="0.5" width="8" height="13" rx="1.5" fill="var(--blossom-pink)"/><rect x="4.5" y="2" width="5" height="8" fill="#fff"/></svg>
      </li>
      <li><span>willowcgather@mailbox.test</span>
        <svg class="contact-icon" viewBox="0 0 14 14" aria-hidden="true"><rect x="0.5" y="2.5" width="13" height="9" fill="var(--blossom-pink)"/><polyline points="1,3 7,8 13,3" fill="none" stroke="#fff" stroke-width="1.2"/></svg>
      </li>
      <li><span>willowcreekgatherings.test</span>
        <svg class="contact-icon" viewBox="0 0 14 14" aria-hidden="true"><circle cx="7" cy="7" r="6.5" fill="var(--blossom-pink)"/><ellipse cx="7" cy="7" rx="2.6" ry="6" fill="none" stroke="#fff" stroke-width="1"/><line x1="1" y1="7" x2="13" y2="7" stroke="#fff" stroke-width="1"/></svg>
      </li>
    </ul>
  </section>

  <section class="card card--back" aria-label="Business card back">
    <svg class="card-art" width="520" height="300" viewBox="0 0 520 300">
      <defs>
        <linearGradient id="orchard-back" x1="0" y1="0" x2="1" y2="1">
          <stop offset="0" stop-color="var(--orchard-green)"/>
          <stop offset="0.4" stop-color="var(--orchard-bloom)"/>
          <stop offset="0.7" stop-color="var(--orchard-sky)"/>
          <stop offset="1" stop-color="var(--orchard-green)"/>
        </linearGradient>
        <linearGradient id="name-band" x1="0" y1="0" x2="0" y2="1">
          <stop offset="0" stop-color="var(--orchard-shade)" stop-opacity="0.85"/>
          <stop offset="1" stop-color="var(--orchard-shade)" stop-opacity="0"/>
        </linearGradient>
      </defs>
      <rect class="orchard-photo" role="img" aria-label="Photo of an almond orchard in bloom, tree rows lining a sunny lane"
            width="520" height="300" fill="url(#orchard-back)"/>
      <rect class="name-band" width="520" height="70" fill="url(#name-band)"/>
    </svg>
    <h2 class="back-name">Maren Lockwood</h2>
  </section>

</main>
</body>
</html>
```